New startup requiring business card

New company needed a business card / logo. Company name is
Brindex
Company is providing IT software sales, partnering and consulting services across the APAC region. Catch line is "growing together".
We currently have a feeling yellow as the primary colour given its meaning across the region but open to ideas. Main brief is we want something smart, clean and professional while still leveraging the strength of the name.
A major part of the business is mutually beneficial partnerships, not sure if this helps but maybe visual around linkages between objects.
Also wanting a standard size card, preference is something that will have a D/S cello sheen finish in a matt. But again open to ideas, wow us!
Industry/Entity Type
Software
Font styles to use
Look and feel

```html
<!DOCTYPE html>
<html lang="en">
<head>
<meta charset="utf-8">
<title>Brindex business card</title>
<link href="https://fonts.googleapis.com/css2?family=Questrial&display=swap" rel="stylesheet">
<style>
  :root {
    --brand-yellow: #ece51c;
    --ink: #2b2b2b;
    --ink-soft: #555555;
    --card: #ffffff;
    --backdrop: #e6e6e4;
    --shadow: rgba(0, 0, 0, 0.14);
  }
  * { box-sizing: border-box; margin: 0; padding: 0; }
  html, body {
    width: 1200px;
    height: 941px;
    overflow: hidden;
    background: var(--backdrop);
    font-family: "Questrial", "Century Gothic", sans-serif;
    color: var(--ink);
  }
  .canvas {
    position: relative;
    width: 1200px;
    height: 941px;
  }
  .card {
    position: absolute;
    background: var(--card);
    box-shadow: 0 6px 22px var(--shadow);
  }

  /* Front: landscape */
  .card-front {
    left: 60px;
    top: 170px;
    width: 600px;
    height: 343px;
  }
  .front-brand {
    position: absolute;
    left: 48px;
    top: 0;
    bottom: 0;
    width: 230px;
    display: flex;
    flex-direction: column;
    justify-content: center;
  }
  .brand-name {
    color: var(--brand-yellow);
    font-size: 52px;
    line-height: 1;
    letter-spacing: 0.5px;
  }
  .brand-tagline {
    margin-top: 8px;
    margin-left: 4px;
    font-size: 13px;
    color: var(--ink-soft);
    letter-spacing: 0.3px;
  }
  .front-details {
    position: absolute;
    left: 320px;
    top: 62px;
    font-size: 12.5px;
    line-height: 1.55;
  }
  .person-name {
    font-size: 16px;
    font-weight: 700;
    color: var(--ink);
    line-height: 1.3;
  }
  .person-role {
    color: var(--brand-yellow);
    font-size: 13px;
    margin-bottom: 12px;
  }
  .address { color: var(--ink); margin-bottom: 16px; }
  .contact-list { list-style: none; }
  .contact-list li {
    display: flex;
    align-items: center;
    gap: 10px;
    line-height: 1.75;
  }
  .contact-icon {
    width: 11px;
    height: 11px;
    flex: none;
  }

  /* Back: portrait */
  .card-back {
    left: 770px;
    top: 250px;
    width: 343px;
    height: 600px;
    display: flex;
    align-items: center;
    justify-content: center;
  }
  .card-back .brand-name { font-size: 64px; }
</style>
</head>
<body>
<main class="canvas">

  <section class="card card-front" aria-label="Business card front">
    <div class="front-brand">
      <div class="brand-name">Brindex</div>
      <div class="brand-tagline">growing together</div>
    </div>

    <div class="front-details">
      <div class="person-name">Mara Ellison</div>
      <div class="person-role">Operations Manager</div>
      <address class="address" style="font-style:normal">
        12 Orchard Row Kensington<br>
        London W8 4QT
      </address>
      <ul class="contact-list">
        <li>
          <svg class="contact-icon" viewBox="0 0 12 12" aria-hidden="true">
            <path d="M2 1.5 L4.2 1.5 L5 4 L3.8 5 Q5 7.4 7 8.2 L8 7 L10.5 7.8 L10.5 10 Q5 10.5 1.5 4 Z" fill="var(--brand-yellow)"/>
          </svg>
          +44 (0)200 000 1234
        </li>
        <li>
          <svg class="contact-icon" viewBox="0 0 12 12" aria-hidden="true">
            <rect x="3" y="0.5" width="6" height="11" rx="1.2" fill="var(--brand-yellow)"/>
            <rect x="4" y="2" width="4" height="6.5" fill="#fff"/>
          </svg>
          +44 (0)7700 900 123
        </li>
        <li>
          <svg class="contact-icon" viewBox="0 0 12 12" aria-hidden="true">
            <rect x="0.5" y="2.5" width="11" height="7.5" rx="1" fill="var(--brand-yellow)"/>
            <path d="M1 3 L6 7 L11 3" stroke="#fff" stroke-width="1" fill="none"/>
          </svg>
          mara.ellison@brindex.co.uk
        </li>
        <li>
          <svg class="contact-icon" viewBox="0 0 12 12" aria-hidden="true">
            <circle cx="6" cy="6" r="5" fill="none" stroke="var(--brand-yellow)" stroke-width="1.4"/>
            <ellipse cx="6" cy="6" rx="2" ry="5" fill="none" stroke="var(--brand-yellow)" stroke-width="1"/>
            <line x1="1" y1="6" x2="11" y2="6" stroke="var(--brand-yellow)" stroke-width="1"/>
          </svg>
          www.brindex.co.uk
        </li>
      </ul>
    </div>
  </section>

  <section class="card card-back" aria-label="Business card back">
    <div class="brand-name">Brindex</div>
  </section>

</main>
</body>
</html>
```